Spiritual Healing bussiness needs logo/business card

Simple, clean looking logo/card
For spiritual business with healing services and occult rituals

Contact Information for Business Card

Needs my name: Tobin Varley
Business name: Lantern Healing Shop
Services provided and worded in this way:

Reiki Healing
Tarot
Oils
Rituals Of Change

Can look occult like but with light energy.

Colors
0255a3
3276b5
85abd2
33a6d7
85cae6
0292cd

```html
<!DOCTYPE html>
<html lang="en">
<head>
<meta charset="utf-8">
<title>Lantern Healing Shop — Business Card</title>
<link href="https://fonts.googleapis.com/css2?family=Oswald:wght@500&family=Work+Sans:wght@400&display=swap" rel="stylesheet">
<style>
  :root {
    --page-bg: #161616;
    --card-bg: #222222;
    --card-sheen: #2e2e2e;
    --brand-blue: #0255a3;
    --accent-blue: #0292cd;
    --ink-light: #f2f2f2;
  }
  * { box-sizing: border-box; margin: 0; padding: 0; }
  html, body {
    width: 1200px; height: 900px; overflow: hidden;
    background: var(--page-bg);
    font-family: "Work Sans", sans-serif;
  }
  .stage {
    position: relative; width: 1200px; height: 900px;
    background: radial-gradient(ellipse at 50% 40%, #2a2a2a 0%, var(--page-bg) 70%);
  }
  .card {
    position: absolute; left: 270px; width: 660px; height: 380px;
    background: linear-gradient(135deg, var(--card-bg) 0%, var(--card-bg) 55%, var(--card-sheen) 85%, var(--card-bg) 100%);
    box-shadow: 0 10px 30px rgba(0,0,0,0.6);
    color: var(--ink-light);
  }
  .card--front { top: 50px; }
  .card--back { top: 470px; }

  .wordmark {
    font-family: "Work Sans", sans-serif;
    font-weight: 400;
    color: var(--ink-light);
    letter-spacing: 3px;
    white-space: nowrap;
    text-align: center;
    position: absolute; left: 0; right: 0;
  }
  .card--front .wordmark { top: 132px; font-size: 36px; }
  .card--back .wordmark { top: 42px; font-size: 34px; }

  .services {
    position: absolute; top: 300px; left: 0; right: 0;
    text-align: center; font-size: 16px; letter-spacing: 1px;
  }
  .services .sep { color: var(--accent-blue); margin: 0 8px; }

  .identity {
    position: absolute; top: 148px; left: 10px; width: 305px;
    text-align: right;
  }
  .identity__name {
    font-family: "Oswald", sans-serif; font-weight: 500;
    font-size: 42px; line-height: 1; letter-spacing: 2px;
    text-transform: uppercase; color: var(--brand-blue);
    white-space: nowrap;
  }
  .identity__role { font-size: 18px; margin-top: 8px; letter-spacing: 1px; }
  .divider {
    position: absolute; top: 150px; left: 335px;
    width: 2px; height: 78px; background: var(--brand-blue);
  }
  .contacts {
    position: absolute; top: 150px; left: 358px;
    list-style: none; font-size: 17px; letter-spacing: 0.5px;
  }
  .contacts li { display: flex; align-items: center; height: 26px; white-space: nowrap; }
  .contacts svg { width: 13px; height: 13px; margin-right: 10px; flex: none; }
  .address {
    position: absolute; top: 300px; left: 0; right: 0;
    text-align: center; font-size: 18px; letter-spacing: 1px;
  }
</style>
</head>
<body>
<div class="stage">

  <section class="card card--front">
    <div class="wordmark">Lantern Healing Shop</div>
    <p class="services">
      Reiki Healing<span class="sep">|</span>Tarot<span class="sep">|</span>Oils<span class="sep">|</span>Rituals Of Change
    </p>
  </section>

  <section class="card card--back">
    <div class="wordmark">Lantern Healing Shop</div>

    <div class="identity">
      <div class="identity__name">Tobin Varley</div>
      <div class="identity__role">Director</div>
    </div>

    <div class="divider"></div>

    <ul class="contacts">
      <li>
        <svg viewBox="0 0 16 16" aria-hidden="true"><path d="M4 1.5 L6.5 4.5 L5 6.5 Q6.5 9.5 9.5 11 L11.5 9.5 L14.5 12 L12.5 14.5 Q5 13.5 1.5 4 Z" fill="var(--brand-blue)"/></svg>
        (204) 613-7790
      </li>
      <li>
        <svg viewBox="0 0 16 16" aria-hidden="true"><rect x="1.5" y="3.5" width="13" height="9" fill="none" stroke="var(--brand-blue)" stroke-width="1.5"/><path d="M1.5 3.5 L8 9 L14.5 3.5" fill="none" stroke="var(--brand-blue)" stroke-width="1.5"/></svg>
        info@lanternhealingshop.com
      </li>
      <li>
        <svg viewBox="0 0 16 16" aria-hidden="true"><circle cx="8" cy="8" r="6.5" fill="none" stroke="var(--brand-blue)" stroke-width="1.4"/><ellipse cx="8" cy="8" rx="2.8" ry="6.5" fill="none" stroke="var(--brand-blue)" stroke-width="1.2"/><path d="M1.5 8 H14.5" stroke="var(--brand-blue)" stroke-width="1.2"/></svg>
        www.lanternhealingshop.com
      </li>
    </ul>

    <p class="address">218b Harlow Street, Westbrook, NZ, 8042</p>
  </section>

</div>
</body>
</html>
```